New Business Card Design Project

Use the flyer uploaded and website www.brightoakbuilders.com for inspiration.
List Our Services on Backside of business cards
Marcus Delling
Harborline Builders Inc.
Licensed General Contractors
858-471-6093

Contact Information for Business Card

Use the flyer uploaded and website www.brightoakbuilders.com for inspiration. List Our Services on Backside of business cards Marcus Delling Harborline Builders Inc. Licensed General Contractors 858-471-6093

```html
<!DOCTYPE html>
<html lang="en">
<head>
<meta charset="utf-8">
<title>Harborline Builders – Business Cards</title>
<link href="https://fonts.googleapis.com/css2?family=Roboto:ital,wght@0,400;0,500;0,700;0,900;1,500;1,700;1,900&display=swap" rel="stylesheet">
<style>
  :root {
    --red: #ec1c24;
    --blue: #2e3192;
    --sky: #3d7fd6;
    --ink: #1a1a1a;
    --paper: #ffffff;
    --backdrop: #e6e6e6;
  }
  * { box-sizing: border-box; margin: 0; padding: 0; }
  html, body { width: 1200px; height: 780px; overflow: hidden; }
  body {
    background: var(--backdrop);
    font-family: "Roboto", Arial, sans-serif;
    color: var(--ink);
    position: relative;
  }
  .card {
    position: absolute;
    top: 236px;
    width: 540px;
    height: 308px;
    background: var(--paper);
    overflow: hidden;
    box-shadow: 0 6px 18px rgba(0,0,0,.18);
  }
  .card--front { left: 40px; }
  .card--back { left: 620px; }

  .wave { position: absolute; inset: 0; }

  .brand {
    position: absolute;
    font-weight: 500;
    font-size: 16px;
    color: var(--ink);
    letter-spacing: 1.5px;
    text-transform: uppercase;
    white-space: nowrap;
  }
  .card--front .brand { left: 296px; top: 52px; }
  .card--back .brand { left: 36px; top: 70px; }

  .person { position: absolute; left: 42px; top: 104px; }
  .person__name { color: var(--red); font-weight: 900; font-size: 30px; line-height: 1; }
  .person__title { font-size: 12.5px; margin-top: 6px; }

  .divider {
    position: absolute; left: 262px; top: 100px;
    width: 1px; height: 92px; background: var(--red);
  }

  .contacts { position: absolute; left: 278px; top: 110px; list-style: none; }
  .contacts li {
    display: flex; align-items: center; gap: 8px;
    font-size: 13px; font-weight: 500; height: 24px;
  }
  .contacts svg { width: 14px; height: 14px; flex: none; }

  .company {
    position: absolute; left: 30px; bottom: 18px;
    color: var(--paper); font-size: 14px; font-weight: 500;
  }

  .services { position: absolute; left: 312px; top: 70px; }
  .services__head { font-weight: 900; font-style: italic; font-size: 14px; line-height: 1.15; text-transform: uppercase; }
  .services__head--red { color: var(--red); }
  .services__head--blue { color: var(--sky); margin-bottom: 6px; }
  .services ul { list-style: none; }
  .services li {
    display: flex; align-items: center; gap: 6px;
    font-style: italic; font-weight: 700; font-size: 11.5px; height: 18px;
    white-space: nowrap;
  }
  .services svg { width: 12px; height: 12px; flex: none; }
</style>
</head>
<body>

<section class="card card--front">
  <svg class="wave" viewBox="0 0 540 308" preserveAspectRatio="none" aria-hidden="true">
    <path d="M0,188 C80,262 290,292 540,276 L540,308 L0,308 Z" fill="var(--red)"/>
    <path d="M10,176 C90,252 300,280 480,272" fill="none" stroke="var(--blue)" stroke-width="3"/>
  </svg>

  <div class="brand">Harborline Builders</div>

  <div class="person">
    <div class="person__name">Marcus Delling</div>
    <div class="person__title">Licensed General Contractors</div>
  </div>

  <div class="divider"></div>

  <ul class="contacts">
    <li>
      <svg viewBox="0 0 16 16"><circle cx="8" cy="8" r="8" fill="var(--red)"/><path d="M5 4.5l1.6-.5 1 2-1 .8a5 5 0 0 0 2.6 2.6l.8-1 2 1-.5 1.6c-3.6.2-6.7-2.9-6.5-6.5z" fill="#fff"/></svg>
      858-471-6093
    </li>
    <li>
      <svg viewBox="0 0 16 16"><circle cx="8" cy="8" r="8" fill="var(--red)"/><rect x="4" y="5" width="8" height="6" fill="none" stroke="#fff" stroke-width="1.2"/><path d="M4 5l4 3.2L12 5" fill="none" stroke="#fff" stroke-width="1.2"/></svg>
      info@brightoakbuilders.com
    </li>
    <li>
      <svg viewBox="0 0 16 16"><circle cx="8" cy="8" r="8" fill="var(--red)"/><circle cx="8" cy="8" r="4.5" fill="none" stroke="#fff" stroke-width="1.1"/><path d="M3.5 8h9M8 3.5c-2 2.5-2 6.5 0 9M8 3.5c2 2.5 2 6.5 0 9" fill="none" stroke="#fff" stroke-width="1"/></svg>
      www.brightoakbuilders.com
    </li>
  </ul>

  <div class="company">Harborline Builders Inc.</div>
</section>

<section class="card card--back">
  <div class="brand">Harborline Builders</div>

  <div class="services">
    <div class="services__head services__head--red">Our services are<br>100% guaranteed</div>
    <div class="services__head services__head--blue">Specializing in:</div>
    <ul>
      <li><svg viewBox="0 0 12 12"><circle cx="6" cy="6" r="5.2" fill="none" stroke="var(--red)" stroke-width="1.2"/><path d="M3.4 6.2l1.8 1.8 3.6-3.8" fill="none" stroke="var(--red)" stroke-width="1.4"/></svg>Remodel: Kitchen &amp; Bath</li>
      <li><svg viewBox="0 0 12 12"><circle cx="6" cy="6" r="5.2" fill="none" stroke="var(--red)" stroke-width="1.2"/><path d="M3.4 6.2l1.8 1.8 3.6-3.8" fill="none" stroke="var(--red)" stroke-width="1.4"/></svg>Painting: Interior &amp; Exterior</li>
      <li><svg viewBox="0 0 12 12"><circle cx="6" cy="6" r="5.2" fill="none" stroke="var(--red)" stroke-width="1.2"/><path d="M3.4 6.2l1.8 1.8 3.6-3.8" fill="none" stroke="var(--red)" stroke-width="1.4"/></svg>Flooring: Carpet, Vinyl, Wood</li>
      <li><svg viewBox="0 0 12 12"><circle cx="6" cy="6" r="5.2" fill="none" stroke="var(--red)" stroke-width="1.2"/><path d="M3.4 6.2l1.8 1.8 3.6-3.8" fill="none" stroke="var(--red)" stroke-width="1.4"/></svg>Window &amp; Door Replacement</li>
      <li><svg viewBox="0 0 12 12"><circle cx="6" cy="6" r="5.2" fill="none" stroke="var(--red)" stroke-width="1.2"/><path d="M3.4 6.2l1.8 1.8 3.6-3.8" fill="none" stroke="var(--red)" stroke-width="1.4"/></svg>Plumbing: Repairs &amp; Upgrades</li>
      <li><svg viewBox="0 0 12 12"><circle cx="6" cy="6" r="5.2" fill="none" stroke="var(--red)" stroke-width="1.2"/><path d="M3.4 6.2l1.8 1.8 3.6-3.8" fill="none" stroke="var(--red)" stroke-width="1.4"/></svg>Energy-Efficient Upgrades</li>
      <li><svg viewBox="0 0 12 12"><circle cx="6" cy="6" r="5.2" fill="none" stroke="var(--red)" stroke-width="1.2"/><path d="M3.4 6.2l1.8 1.8 3.6-3.8" fill="none" stroke="var(--red)" stroke-width="1.4"/></svg>Deck &amp; Patio Construction</li>
      <li><svg viewBox="0 0 12 12"><circle cx="6" cy="6" r="5.2" fill="none" stroke="var(--red)" stroke-width="1.2"/><path d="M3.4 6.2l1.8 1.8 3.6-3.8" fill="none" stroke="var(--red)" stroke-width="1.4"/></svg>Water &amp; Mold Damage</li>
      <li><svg viewBox="0 0 12 12"><circle cx="6" cy="6" r="5.2" fill="none" stroke="var(--red)" stroke-width="1.2"/><path d="M3.4 6.2l1.8 1.8 3.6-3.8" fill="none" stroke="var(--red)" stroke-width="1.4"/></svg>Garage Renovation</li>
    </ul>
  </div>
</section>

</body>
</html>
```